Build a landing page to promote a service (dialler consultation and support).

We are a call centre consultation firm and we need a landing page to promote a service. The service is Tormalux dialler consultation and support.
If you do not know what Tormalux is, please do some quick "Zorvex" research for more information.
The landing page will be promoted with a paid advertisement, so we want something that is simple, and explains exactly what service we offer.
There are two objectives for the landing page:
1) A "call to action" which directs the user to a contact page, including a form plus all of our contact details.
2) A form for them viewers to enter their details to get a "FREE" quote for their project. This form should be placed on the main page.
Notes:
The call to action will require the viewer to enter their name, email, phone number as well as a description of their request. There will also need to be a drop down menu for the type of quote. This menu should have the following options:
1) Tormalux support
2) Tormalux hosting
3) Tormalux customisation
4) Other
We need 2 pages in total:
1) Main landing page
This is the home page. It will need to clearly indicate our services and our key selling features.
Services:
* Tormalux support
* Tormalux hosting
* Tormalux customisation
Key Selling Features:
* Australian based
* PCI complaint
* 10+ years of dialler and call centre experience
* we run a sister company which is a highly reputable 40 seat call centre, so we know first hand about call centre technology.
The main landing page will have an "about us" section with a few paragraphs about how we got started.
-------------------------------------------------------------------------
2) Contact page
All of our contact details will live on this page, as well as a contact form.
Other notes:
We will be self hosting the landing page.
We already have a domain name.
The design must be clean and incorporate our logo, as well as it's colours. (Logo attached)
We want a fully function HTML landing page, not just a "PSD" design.
The page must be mobile optimised.
Anyone using Tormalux software.

```html
<!DOCTYPE html>
<html lang="en">
<head>
<meta charset="utf-8">
<title>Quellin — Tormalux support and call centre technology</title>
<link href="https://fonts.googleapis.com/css2?family=Montserrat:wght@500;600&family=PT+Sans:wght@700&family=Lato:wght@400;700&display=swap" rel="stylesheet">
<style>
  :root {
    --page-bg: #ffffff;
    --ink: #2b2b2b;
    --brand-blue: #4a9fd0;
    --coral: #e9836a;
    --hero-deep: #3f6d99;
    --hero-mid: #5b87b3;
    --hero-light: #7fa3c6;
    --white: #ffffff;
  }
  * { box-sizing: border-box; margin: 0; padding: 0; }
  html, body {
    width: 1200px;
    height: 813px;
    overflow: hidden;
    background: var(--page-bg);
  }
  .site {
    width: 1200px;
    height: 813px;
    position: relative;
  }
  .site-header {
    height: 60px;
    display: flex;
    align-items: center;
    padding: 0 61px;
    background: var(--page-bg);
  }
  .brand {
    text-decoration: none;
    font-family: "Montserrat", sans-serif;
    font-weight: 500;
    font-size: 24px;
    letter-spacing: 1px;
    color: var(--brand-blue);
  }
  .main-nav {
    margin-left: auto;
    display: flex;
    align-items: center;
    gap: 33px;
  }
  .main-nav a {
    font-family: "Montserrat", sans-serif;
    font-weight: 500;
    font-size: 14px;
    letter-spacing: 1.3px;
    color: var(--ink);
    text-decoration: none;
  }
  .main-nav .nav-cta {
    margin-left: -8px;
    margin-right: -4px;
    width: 198px;
    height: 38px;
    border-radius: 19px;
    background: var(--coral);
    color: var(--white);
    font-weight: 600;
    display: flex;
    align-items: center;
    justify-content: center;
  }
  .hero {
    position: relative;
    height: 753px;
    overflow: hidden;
  }
  .hero-photo {
    position: absolute;
    inset: 0;
    background:
      radial-gradient(ellipse at 75% 35%, var(--hero-light) 0%, transparent 55%),
      linear-gradient(180deg, var(--hero-mid) 0%, var(--hero-deep) 70%, var(--hero-mid) 100%);
  }
  .hero-content {
    position: relative;
    padding: 123px 0 0 77px;
    color: var(--white);
  }
  .hero-title {
    font-family: "PT Sans", sans-serif;
    font-weight: 700;
    font-size: 59px;
    line-height: 66px;
    width: 620px;
  }
  .hero-lead {
    margin-top: 30px;
    font-family: "Lato", sans-serif;
    font-size: 20px;
    line-height: 32px;
    width: 560px;
  }
  .hero-cta {
    display: inline-flex;
    align-items: center;
    justify-content: center;
    margin-top: 44px;
    width: 245px;
    height: 51px;
    border-radius: 26px;
    background: var(--coral);
    color: var(--white);
    font-family: "Lato", sans-serif;
    font-weight: 700;
    font-size: 17px;
    letter-spacing: 0.6px;
    text-decoration: none;
  }
</style>
</head>
<body>
<div class="site">
  <header class="site-header">
    <a class="brand" href="#">Quellin</a>
    <nav class="main-nav">
      <a href="#">SERVICES</a>
      <a href="#">ABOUT US</a>
      <a href="#">WHY QUELLIN</a>
      <a href="#">CONTACT US</a>
      <a class="nav-cta" href="#">GET A QUOTE</a>
    </nav>
  </header>
  <section class="hero">
    <div class="hero-photo" role="img" aria-label="Call centre agents wearing headsets working at computer monitors, tinted blue"></div>
    <div class="hero-content">
      <h1 class="hero-title">A holistic approach to Tormalux support and call centre technology</h1>
      <p class="hero-lead">A complete Tormalux call center consultation for better service, productivity and profitability.</p>
      <a class="hero-cta" href="#">GET A FREE QUOTE</a>
    </div>
  </section>
</div>
</body>
</html>
```